Stationery Design Project for Nimbora, Chicago

Nimbora, a street parking application which helps car drivers find a street parking spot by offering an ideal path along which to look for parking. This path is calculated by our algorithm based on data (e.g. historical data, baseball games schedule, etc.). Along this path the driver will find a spot and will also save 70% of the search time. Customer we target is reg. between 21 and 45 yo.

We envision something young, fresh, bright and original. Slightly abstract maybe. It should represent the idea and elements of finding street parking in the city, e.g. car(s), parking spot, people, city, etc. (just ideas!).

Logo is attached.

Requirement:
- Business Cards (2 Sided Full Color CMYK)
- Letterhead (1 Sided Full Color CMYK)
- Envelope (1 Sided Full Color CMYK)
- Sticker (1 Sided Full Color CMYK), round with a 2inch diameter.

Reason: We're starting to get more and more designs and need more time to look into all of them. Very exciting!! Thanks to everybody!

Hi all, we're in the process of selecting our favs. Though choices!!! Really good submissions. Will keep you posted and sorry for the delay.

Target Market(s)

Car drivers and owners between 21 and 45

Industry/Entity Type

Parking

Requirements
Must have
• Sticker should be round and include company URL nimbora.com and the new logo which we will attach soon.
Should not have
• Should not be too serious or boring.

```html
<!DOCTYPE html>
<html lang="en">
<head>
<meta charset="utf-8">
<title>Nimbora business card</title>
<link rel="stylesheet" href="https://fonts.googleapis.com/css2?family=Open+Sans:wght@400;600;700&display=swap">
<style>
  :root {
    --page-bg: #e9e7e4;
    --card-bg: #ffffff;
    --ink-dark: #1e1e1e;
    --ink-grey: #4d4d4d;
    --brand-navy: #1f3f8f;
    --brand-blue: #2c5fb8;
    --brand-sky: #3fa3e0;
    --swoosh-dark: #2a2a2a;
  }
  * { box-sizing: border-box; margin: 0; padding: 0; }
  html, body { width: 1200px; height: 758px; overflow: hidden; }
  body {
    background: var(--page-bg);
    font-family: "Open Sans", Arial, sans-serif;
    position: relative;
  }
  .card {
    position: absolute;
    width: 520px;
    height: 298px;
    background: var(--card-bg);
    border-radius: 24px;
    box-shadow: 0 8px 24px rgba(0,0,0,.18);
    overflow: hidden;
  }
  .card--front { left: 50px; top: 230px; }
  .card--back { left: 630px; top: 230px; }

  .brand {
    position: absolute;
    display: flex;
    align-items: center;
    gap: 16px;
  }
  .brand__dot {
    border-radius: 50%;
    background: var(--brand-blue);
    flex: none;
  }
  .brand__name {
    font-weight: 600;
    color: var(--ink-dark);
    letter-spacing: 0.5px;
  }
  .card--front .brand { left: 40px; top: 34px; }
  .card--front .brand__dot { width: 84px; height: 84px; }
  .card--front .brand__name { font-size: 58px; line-height: 1; }

  .wave { position: absolute; left: 0; bottom: 0; width: 520px; height: 170px; }

  .holder {
    position: absolute;
    left: 44px;
    top: 158px;
    font-size: 16px;
    color: var(--brand-navy);
    font-weight: 700;
  }
  .holder__title { font-weight: 400; font-size: 12px; color: var(--ink-grey); }

  .contacts {
    position: absolute;
    left: 44px;
    top: 186px;
    list-style: none;
    font-size: 12px;
    line-height: 17px;
    color: var(--ink-grey);
  }
  .contacts li { display: flex; align-items: center; gap: 6px; }
  .contacts svg { width: 9px; height: 9px; fill: var(--ink-grey); }

  .address {
    position: absolute;
    right: 34px;
    top: 224px;
    text-align: right;
    color: #fff;
    font-size: 12px;
    line-height: 17px;
  }

  .card--back .brand {
    left: 0; right: 0; top: 52px;
    flex-direction: column;
    gap: 10px;
  }
  .card--back .brand__dot { width: 120px; height: 120px; }
  .card--back .brand__name { font-size: 22px; }
  .site {
    position: absolute;
    left: 0; right: 0; bottom: 38px;
    text-align: center;
    font-size: 26px;
    font-weight: 700;
    letter-spacing: 4px;
    color: var(--ink-grey);
  }
</style>
</head>
<body>
  <section class="card card--front">
    <div class="brand">
      <span class="brand__dot"></span>
      <span class="brand__name">nimbora</span>
    </div>

    <svg class="wave" viewBox="0 0 520 170" aria-hidden="true">
      <defs>
        <linearGradient id="waveFill" x1="0" y1="0" x2="1" y2="0">
          <stop offset="0" stop-color="var(--brand-sky)"/>
          <stop offset="1" stop-color="var(--brand-navy)"/>
        </linearGradient>
      </defs>
      <path d="M0 150 C 200 158, 300 80, 520 30 L 520 170 L 0 170 Z" fill="url(#waveFill)"/>
      <path d="M200 124 C 300 84, 400 30, 520 12 L 520 20 C 410 38, 310 92, 200 124 Z" fill="var(--swoosh-dark)"/>
    </svg>

    <p class="holder">Your Name, <span class="holder__title">Title</span></p>
    <ul class="contacts">
      <li><svg viewBox="0 0 10 10"><path d="M2 0h2l1 3-1.5 1a6 6 0 0 0 2.5 2.5L7 5l3 1v2a2 2 0 0 1-2 2A8 8 0 0 1 0 2a2 2 0 0 1 2-2z"/></svg>123-456-789</li>
      <li><svg viewBox="0 0 10 10"><rect x="2.5" y="0" width="5" height="10" rx="1"/></svg>123-456-789</li>
      <li><svg viewBox="0 0 10 10"><rect x="0" y="2" width="10" height="6"/></svg>info@nimbora.com</li>
      <li><svg viewBox="0 0 10 10"><circle cx="5" cy="5" r="5"/></svg>www.nimbora.com</li>
    </ul>
    <p class="address">Complex name, Street name<br>City, State, zip code</p>
  </section>

  <section class="card card--back">
    <div class="brand">
      <span class="brand__dot"></span>
      <span class="brand__name">nimbora</span>
    </div>
    <p class="site">www.nimbora.com</p>
  </section>
</body>
</html>
```